International oil and gas consultancy needs a business card design

We need a business card design for a new oil and gas consultancy business based in Perth Australia. This is a professional services business and needs a moderately conservative type of business card. The business card also needs to be simple and uncluttered. The colour of the business logo is dark red (see attached file).
The front of the card should have a white background and mainly black lettering and perhaps some use of dark red and/or grey (your choice).
The back of the card should have a light grey background with dark red, black and or both dark red & black lettering (your choice).
Please find attached a clear brief of how I would like the business card designed.
Updates

Hello Everyone, I have slightly modified the brief. The main change is to incorporate some dark red and grey colours into the card, while still keeping the black lettering dominant. I have made the changes in the attached detailed brief document. Regards

Please note, the front of the card must say Harbour Ledger Services (in addition to the logo).

Industry/Entity Type

Conservative

Requirements
Must have
• brief has been updated. please refer to attachment for details.

Front of the card MUST say Harbour Ledger Services (in addition to the logo)

```html
<!DOCTYPE html>
<html lang="en">
<head>
<meta charset="utf-8">
<title>Harbour Ledger Services – Business Card</title>
<link rel="stylesheet" href="https://fonts.googleapis.com/css2?family=Arimo:wght@400;700&display=swap">
<style>
  :root {
    --stage: #ecebe8;
    --card-white: #ffffff;
    --grey-dark: #6a6a6a;
    --grey-light: #8d8d8d;
    --brand-red: #9b1c24;
    --ink: #1f1f1f;
    --ink-soft: #3a3a3a;
    --divider: #9a9a9a;
  }
  * { box-sizing: border-box; margin: 0; padding: 0; }
  html, body {
    width: 1200px; height: 784px; overflow: hidden;
    background: var(--stage);
    font-family: "Arimo", Arial, sans-serif;
  }
  .stage { position: relative; width: 1200px; height: 784px; }

  .card {
    position: absolute; width: 540px; height: 330px; top: 227px;
    box-shadow: 0 6px 18px rgba(0,0,0,0.18);
    overflow: hidden;
  }

  /* Back of card */
  .card-back {
    left: 40px;
    background: linear-gradient(135deg, var(--grey-light), var(--grey-dark));
  }
  .card-back .wordmark {
    position: absolute; top: 42px; left: 0; width: 100%;
    text-align: center; color: var(--brand-red);
    font-weight: 700; font-size: 58px; letter-spacing: 2px;
  }
  .services {
    position: absolute; top: 132px; left: 178px; list-style: none;
  }
  .services li {
    color: #ffffff; font-size: 15px; line-height: 30px;
    padding-left: 18px; position: relative;
  }
  .services li::before {
    content: ""; position: absolute; left: 0; top: 12px;
    width: 6px; height: 6px; border-radius: 50%; background: var(--brand-red);
  }
  .tagline {
    position: absolute; bottom: 42px; left: 0; width: 100%; text-align: center;
    color: var(--brand-red); font-weight: 700; font-size: 13.5px; letter-spacing: 0.6px;
  }

  /* Front of card */
  .card-front { left: 620px; background: var(--card-white); }
  .card-front .wordmark {
    position: absolute; top: 34px; left: 150px;
    color: var(--brand-red); font-weight: 700; font-size: 78px; letter-spacing: 3px;
  }
  .rule-top {
    position: absolute; top: 118px; left: 0; width: 100%; height: 4px; background: var(--brand-red);
  }
  .company-name {
    position: absolute; top: 132px; left: 128px;
    color: var(--ink-soft); font-size: 24px;
  }
  .person {
    position: absolute; right: 278px; top: 190px; text-align: right;
  }
  .person-name { color: var(--brand-red); font-size: 22px; }
  .rule-band {
    position: absolute; top: 222px; left: 0; width: 265px; height: 7px; background: var(--brand-red);
  }
  .role {
    position: absolute; right: 278px; top: 236px; text-align: right;
    color: var(--ink); font-size: 14px; line-height: 19px;
  }
  .role .region { font-weight: 700; }
  .divider {
    position: absolute; left: 275px; top: 178px; width: 1px; height: 110px; background: var(--divider);
  }
  .contacts {
    position: absolute; left: 290px; top: 180px; list-style: none;
  }
  .contacts li {
    display: flex; align-items: center; gap: 7px;
    color: var(--ink); font-size: 13px; line-height: 20px;
  }
  .contacts svg { width: 12px; height: 12px; flex: none; }
  .contacts .plain { padding-left: 19px; }
</style>
</head>
<body>
<main class="stage">

  <section class="card card-back" aria-label="Back of business card">
    <div class="wordmark">HLS</div>
    <ul class="services">
      <li>Joint Venture Audits</li>
      <li>Contract Audits</li>
      <li>Operational Audits</li>
    </ul>
    <p class="tagline">SPECIALIST FINANCIAL CONSULTANTS TO THE OIL AND GAS INDUSTRY</p>
  </section>

  <section class="card card-front" aria-label="Front of business card">
    <div class="wordmark">HLS</div>
    <div class="rule-top"></div>
    <p class="company-name">Harbour Ledger Services</p>

    <div class="person"><p class="person-name">Neil Garrow</p></div>
    <div class="rule-band"></div>
    <div class="role">
      <p>Director</p>
      <p class="region">Australasia and South East Asia</p>
    </div>

    <div class="divider"></div>
    <ul class="contacts">
      <li>
        <svg viewBox="0 0 12 12" aria-hidden="true"><path d="M6 1 L11 5.5 H9.5 V11 H7 V8 H5 V11 H2.5 V5.5 H1 Z" fill="var(--brand-red)"/></svg>
        N/A for the business card
      </li>
      <li>
        <svg viewBox="0 0 12 12" aria-hidden="true"><path d="M2.5 1 L4.5 1 L5.3 3.6 L4 4.6 Q5 7 7.4 8 L8.4 6.7 L11 7.5 L11 9.5 Q10.5 11 9 11 Q2 10 1 3 Q1 1.5 2.5 1 Z" fill="var(--brand-red)"/></svg>
        +61 (0)400 318 522
      </li>
      <li>
        <svg viewBox="0 0 12 12" aria-hidden="true"><rect x="1" y="2.5" width="10" height="7" rx="1" fill="var(--brand-red)"/><path d="M1.5 3 L6 6.5 L10.5 3" stroke="#fff" stroke-width="1" fill="none"/></svg>
        neil@harbourledger.com
      </li>
      <li>
        <svg viewBox="0 0 12 12" aria-hidden="true"><circle cx="6" cy="6" r="5" fill="var(--brand-red)"/><path d="M1 6 H11 M6 1 V11 M2 3.5 H10 M2 8.5 H10" stroke="#fff" stroke-width="0.7" fill="none"/><ellipse cx="6" cy="6" rx="2.2" ry="5" stroke="#fff" stroke-width="0.7" fill="none"/></svg>
        www.harbourledger.com
      </li>
      <li class="plain">ABN: 51 204 776 390</li>
    </ul>
  </section>

</main>
</body>
</html>
```